Carpet cleaning company focused on high quality needs business cards

We are a growing company that just merged with another company and need to design a new business card. We do both residential as well as commercial cleaning. We do carpet, tile & grout, upholstery, hard floors, and stain & pet odor removal. We treat our customers like family and strive to achieve outstanding results with every job.

```html
<!DOCTYPE html>
<html lang="en">
<head>
<meta charset="utf-8">
<title>Brightway Floorcare – Business Card</title>
<link rel="stylesheet" href="https://fonts.googleapis.com/css2?family=Open+Sans:wght@400;600;800&display=swap">
<style>
  :root {
    --backdrop: #232323;
    --card: #ffffff;
    --accent: #ee4540;
    --ink: #111111;
    --muted: #222222;
  }
  * { box-sizing: border-box; margin: 0; padding: 0; }
  html, body { width: 1200px; height: 780px; overflow: hidden; }
  body {
    background: var(--backdrop);
    font-family: "Open Sans", Arial, sans-serif;
    color: var(--ink);
    display: flex;
    align-items: center;
    justify-content: center;
    gap: 40px;
  }
  .card {
    position: relative;
    width: 540px;
    height: 310px;
    background: var(--card);
    overflow: hidden;
  }
  .edge-bar {
    position: absolute;
    width: 11px;
    background: var(--accent);
  }
  .edge-bar--left { left: 0; top: 118px; height: 128px; }
  .edge-bar--right { right: 0; top: 38px; height: 112px; }

  .brand-name {
    position: absolute;
    font-weight: 800;
    color: var(--ink);
    white-space: nowrap;
    line-height: 1.1;
  }
  .card--front .brand-name {
    left: 0;
    right: 0;
    top: 134px;
    text-align: center;
    font-size: 34px;
  }
  .card--back .brand-name {
    left: 40px;
    top: 140px;
    font-size: 19px;
  }

  .divider {
    position: absolute;
    left: 268px;
    top: 46px;
    width: 1.5px;
    height: 150px;
    background: var(--ink);
    transform: rotate(-12deg);
  }
  .contact {
    position: absolute;
    left: 300px;
    top: 52px;
  }
  .contact__name {
    font-size: 25px;
    font-weight: 800;
    line-height: 1.1;
    color: var(--ink);
  }
  .contact__name .first { color: var(--accent); }
  .contact__role {
    font-size: 13px;
    font-weight: 600;
    color: var(--muted);
    margin-top: 2px;
  }
  .contact__list {
    list-style: none;
    margin-top: 18px;
    font-size: 13px;
    color: var(--muted);
  }
  .contact__list li {
    display: flex;
    align-items: center;
    gap: 8px;
    margin-bottom: 4px;
  }
  .contact__list svg { width: 13px; height: 13px; fill: var(--accent); flex: none; }
  .address {
    position: absolute;
    left: 150px;
    top: 236px;
    font-size: 14px;
    color: var(--muted);
    letter-spacing: 0.2px;
  }
</style>
</head>
<body>

  <section class="card card--front" aria-label="Card front">
    <span class="edge-bar edge-bar--left"></span>
    <span class="edge-bar edge-bar--right"></span>
    <p class="brand-name">Brightway Floorcare</p>
  </section>

  <section class="card card--back" aria-label="Card back">
    <span class="edge-bar edge-bar--left"></span>
    <span class="edge-bar edge-bar--right"></span>
    <p class="brand-name">Brightway Floorcare</p>
    <span class="divider"></span>
    <div class="contact">
      <h1 class="contact__name"><span class="first">Marta</span> Velinova</h1>
      <p class="contact__role">Managing Director</p>
      <ul class="contact__list">
        <li>
          <svg viewBox="0 0 24 24" aria-hidden="true"><path d="M6.6 10.8a15.1 15.1 0 0 0 6.6 6.6l2.2-2.2a1 1 0 0 1 1-.25 11.4 11.4 0 0 0 3.6.57 1 1 0 0 1 1 1V20a1 1 0 0 1-1 1A17 17 0 0 1 3 4a1 1 0 0 1 1-1h3.5a1 1 0 0 1 1 1 11.4 11.4 0 0 0 .57 3.6 1 1 0 0 1-.25 1z"/></svg>
          (555) 014-2290
        </li>
        <li>
          <svg viewBox="0 0 24 24" aria-hidden="true"><path d="M2 5h20v14H2zm2 2v.5l8 5 8-5V7l-8 5z"/></svg>
          hello@brightwayfloor.com
        </li>
        <li>
          <svg viewBox="0 0 24 24" aria-hidden="true"><path d="M12 2a10 10 0 1 0 0 20 10 10 0 0 0 0-20zm6.9 6h-3a15 15 0 0 0-1.3-3.9A8 8 0 0 1 18.9 8zM12 4a13 13 0 0 1 1.9 4h-3.8A13 13 0 0 1 12 4zM4.3 14a8 8 0 0 1 0-4h3.4a16 16 0 0 0 0 4zm.8 2h3a15 15 0 0 0 1.3 3.9A8 8 0 0 1 5.1 16zm3-8h-3a8 8 0 0 1 4.3-3.9A15 15 0 0 0 8.1 8zM12 20a13 13 0 0 1-1.9-4h3.8A13 13 0 0 1 12 20zm2.3-6H9.7a14 14 0 0 1 0-4h4.6a14 14 0 0 1 0 4zm.3 5.9a15 15 0 0 0 1.3-3.9h3a8 8 0 0 1-4.3 3.9zm1.7-5.9a16 16 0 0 0 0-4h3.4a8 8 0 0 1 0 4z"/></svg>
          www.brightwayfloor.com
        </li>
      </ul>
    </div>
    <p class="address">418 Elm Grove Ave Dalton, Texas 75390 USA</p>
  </section>

</body>
</html>
```